Verpackungen für Parfum-Proben
Besten Dank! Das Team ist begeistert - also bin ich es auch und wir freuen uns schon, unsere Parfum Proben in Zukunft in diesem tollen Design weitergeben zu können! Danke!
Zielgruppe
Hallo allerseits! Wir sind im Direktvertrieb in den Bereichen Parfum & Kosmetik tätig.
Aufgabenstellung
Für unsere Parfum-Proben benötige ich ein ansprechendes, modernes Design.
Das Design muss relativ neutral gehalten werden, da die Blister sowohl für Herren- als auch Damenproben verwendet werden.
Auf Vorder- und Rückseite soll unser Team-Logo (NaseNomade®) sichtbar sein (Vorderseite größer, Rückseite kleiner).
Auf der linken Innenseite sollte Plätz für einen netten Spruch (den ich mir noch überlege) sein.
Auf der Rückseite muss Platz (weißes / helles Feld) für einen Stempel und/oder Aufkleber (Kontaktdaten des Distributors) sein.
Unser Logo ist Lila - Das farbliche Design sollte dazu passen.
Bei Fragen, einfach Nachricht :)
Daten:
Endformat: 133 x 74 mm
Datenformat: 139 x 80 mm
1-teilig, gestanzt, genutet, einseitig geklebt geliefert
Bitte verwenden Sie für positive Schriftstärken mindestens 9pt (ca. 3,17mm) und bei negativen Schriftstärken mindestens 13pt (ca. 4,59mm).
Abmessungen / Druck- / Designvorlage, Logo, etc.: https://dateiwolke-beispiel.de/ordner/X7pLrT2k#v9wQe4nZb6Hs1Ym_d8cKfa

```html
<!DOCTYPE html>
<html lang="de">
<head>
<meta charset="utf-8">
<title>NaseNomade – Parfum-Proben Blister</title>
<link rel="stylesheet" href="https://fonts.googleapis.com/css2?family=Montserrat:wght@500;600;700&display=swap">
<style>
  :root {
    --bg: #f4f4f6;
    --lavender: #8a89a7;
    --lavender-dark: #777592;
    --lavender-light: #a3a2bc;
    --slot: #6f6d8a;
    --paper: #e9e9ee;
    --logo-purple: #5a3d91;
    --ink: #1e1e26;
  }
  * { box-sizing: border-box; margin: 0; padding: 0; }
  html, body { width: 1200px; height: 800px; overflow: hidden; }
  body {
    background: var(--bg);
    font-family: "Montserrat", sans-serif;
    color: var(--ink);
    display: flex;
    flex-direction: column;
    align-items: center;
    justify-content: center;
    gap: 56px;
  }
  .sheet {
    width: 1040px;
    height: 300px;
    display: flex;
    box-shadow: 0 10px 30px rgba(60, 58, 90, 0.18);
  }
  .panel {
    position: relative;
    width: 480px;
    height: 100%;
    display: flex;
    align-items: center;
    justify-content: center;
  }
  .panel--pattern {
    background: linear-gradient(135deg, var(--lavender-light) 0%, var(--lavender) 50%, var(--lavender-dark) 100%);
  }
  .panel--plain { background: var(--lavender); }
  .spine {
    width: 80px;
    height: 100%;
    background: var(--lavender-dark);
    display: flex;
    align-items: center;
    justify-content: center;
  }
  .vial-window {
    width: 44px;
    height: 210px;
    border-radius: 8px;
    background: var(--paper);
    display: flex;
    align-items: center;
    justify-content: center;
  }
  .vial-window span {
    writing-mode: vertical-rl;
    font-size: 12px;
    font-weight: 600;
    color: var(--logo-purple);
  }
  .tab-slots {
    width: 80px;
    height: 100%;
    background: var(--lavender-dark);
    display: flex;
    flex-direction: column;
    justify-content: space-evenly;
    align-items: center;
  }
  .tab-slots i {
    display: block;
    width: 40px;
    height: 44px;
    border-radius: 6px;
    background: var(--slot);
  }
  .pattern-fill { position: absolute; inset: 0; }
  .label-front {
    position: relative;
    width: 210px;
    height: 210px;
    background: var(--paper);
    border: 2px solid var(--logo-purple);
    display: flex;
    flex-direction: column;
    align-items: center;
    justify-content: center;
    gap: 34px;
  }
  .brand {
    display: flex;
    align-items: center;
    gap: 8px;
    font-size: 26px;
    font-weight: 600;
    color: var(--logo-purple);
  }
  .brand__dot {
    width: 14px; height: 14px; border-radius: 50%;
    background: var(--logo-purple);
  }
  .brand--small { font-size: 18px; color: var(--ink); }
  .brand--small .brand__dot { width: 10px; height: 10px; background: var(--ink); }
  .claim {
    font-size: 10px;
    font-weight: 700;
    letter-spacing: 0.3em;
    text-align: center;
    line-height: 1.6;
  }
  .label-back {
    position: relative;
    width: 200px;
    height: 250px;
    background: var(--paper);
    border: 2px solid var(--logo-purple);
    padding: 20px 14px;
    display: flex;
    flex-direction: column;
    align-items: center;
    gap: 14px;
    text-align: center;
  }
  .label-back p {
    font-size: 8px;
    font-weight: 700;
    line-height: 1.5;
  }
  .stamp-field {
    margin-top: auto;
    width: 100%;
    height: 70px;
    background: #f7f7fa;
    border: 1px solid #d4d4dc;
  }
  .claim--inside { font-size: 11px; font-weight: 600; }
</style>
</head>
<body>
  <section class="sheet sheet--outside" aria-label="Außenseite">
    <div class="panel panel--pattern">
      <div class="pattern-fill" role="img" aria-label="Dekoratives Muster aus fließenden Linien und Flächen in Lavendeltönen"></div>
      <div class="label-front">
        <div class="brand"><span class="brand__dot"></span>NaseNomade</div>
        <div class="claim">ENTDECKE DEINEN<br>DUFT</div>
      </div>
    </div>
    <div class="spine">
      <div class="vial-window"><span>NaseNomade</span></div>
    </div>
    <div class="panel panel--pattern">
      <div class="pattern-fill" role="img" aria-label="Dekoratives Muster aus fließenden Linien und Flächen in Lavendeltönen"></div>
      <div class="label-back">
        <p>LAOREET DOLORE MAGNA</p>
        <p>LOREM IPSUM DOLOR SIT AMET,<br>CONSECTETUER ADIPISCING ELIT, SED DIAM NONUMMY</p>
        <div class="brand brand--small"><span class="brand__dot"></span>NaseNomade</div>
        <div class="stamp-field"></div>
      </div>
    </div>
  </section>

  <section class="sheet sheet--inside" aria-label="Innenseite">
    <div class="panel panel--plain"></div>
    <div class="tab-slots"><i></i><i></i><i></i></div>
    <div class="panel panel--plain">
      <div class="claim claim--inside">ENTDECKE DEINEN<br>DUFT</div>
    </div>
  </section>
</body>
</html>
```